Informational Site for Advanced Chemistry R&D

The company develops oxidation chemistry for air, water, fuel pollution controls. The site has been prototyped at www.velquaresearch.example. Take a look. Now, the task is to design it for eye-catching beauty with use of color, on-page scroll-driven color transition and parallax effects. Should capture the themes: high technology, wow it's beautiful, modern, uncluttered, clean urban environment.

Target Market(s)

China Environmentally Conscious Government and Industry,

Industry/Entity Type

It Company

Number of Pages Required

3 page

Font styles to use
Sans Serif

Requirements
Must have
• Parallax effects, desktop compatible, Rich, Modern, Simple, Graphic
Nice to have
• Mobile Phone Compatible
Should not have
• Flash, or anything that is slow to load or requires high bandwidth

```html
<!DOCTYPE html>
<html lang="en">
<head>
<meta charset="utf-8">
<title>Velqua Research — Advanced Oxidation Science</title>
<link rel="stylesheet" href="https://fonts.googleapis.com/css2?family=Open+Sans:wght@400;600;700&family=Roboto:wght@300;400;500;700&display=swap">
<style>
:root{
  --blue:#1c6cc0;
  --blue-band:#2174c9;
  --teal:#2bbdb4;
  --white:#ffffff;
  --ink:#3d4650;
  --grey-panel:#eceeef;
  --footer:#5b5b5b;
  --oxid-a:#2f5a62;
  --oxid-b:#7b9c8f;
}
*{box-sizing:border-box;margin:0;padding:0}
html,body{width:1200px;height:3516px;overflow:hidden}
body{font-family:"Roboto",Arial,sans-serif;color:var(--white);position:relative;background:var(--white)}
a{text-decoration:none;color:inherit}
.section{position:absolute;left:0;width:1200px;overflow:hidden}
.section-title{position:absolute;left:0;width:1200px;text-align:center;font-family:"Open Sans",Arial,sans-serif;font-weight:700;font-size:22px;letter-spacing:.5px}
.section-title::after{content:"";display:block;width:74px;height:3px;background:currentColor;margin:12px auto 0}

/* hero */
.hero{top:0;height:598px}
.hero-art{position:absolute;inset:0;background:linear-gradient(100deg,#8fb2c4 0,#a9c6d2 25%,#6e9a86 48%,#3f6a58 62%,#1e3556 80%,#0d1a33 100%)}
.logo-box{position:absolute;left:160px;top:0;width:144px;height:117px;background:rgba(255,255,255,.25);display:flex;flex-direction:column;align-items:center;justify-content:center;gap:8px}
.logo-box .mark{width:34px;height:34px;border-radius:50%;background:var(--white)}
.logo-box .name{font-size:16px;font-weight:500;color:var(--white)}
.main-nav{position:absolute;right:150px;top:16px;display:flex;font-size:13px;font-weight:700;letter-spacing:.5px}
.main-nav a{color:var(--white);padding:0 20px;border-left:1px solid rgba(255,255,255,.7)}
.main-nav a:first-child{border-left:none}
.hero-tagline{position:absolute;left:605px;top:434px;width:346px;text-align:center;font-size:27px;font-weight:300;line-height:34px;text-shadow:0 1px 4px rgba(0,0,0,.4)}
.hero-dots{position:absolute;left:565px;top:548px;display:flex;gap:16px}
.hero-dots span{width:10px;height:10px;border-radius:50%;background:var(--white)}
.hero-dots span:first-child{background:transparent;border:2px solid var(--white)}

/* ideas */
.ideas{top:598px;height:598px}
.ideas-art{position:absolute;inset:0;background:linear-gradient(180deg,#2a63b8 0,#4b86cc 35%,#8aa6b3 60%,#3d6a82 78%,#20344a 100%)}
.ideas .section-title{top:28px}
.solutions-panel{position:absolute;left:411px;top:147px;width:374px;height:403px;background:rgba(28,108,192,.85);border:1px solid rgba(255,255,255,.25)}
.panel-head{text-align:center;font-size:18px;font-weight:700;padding-top:18px;text-decoration:underline;text-underline-offset:6px}
.panel-tops{display:grid;grid-template-columns:repeat(3,1fr);margin-top:22px;height:80px}
.panel-tops div{display:flex;flex-direction:column;align-items:center;gap:8px;font-size:15px;font-weight:700}
.panel-grid{display:grid;grid-template-columns:repeat(3,1fr);grid-template-rows:repeat(2,114px);margin-top:22px;border-top:1px solid rgba(255,255,255,.35)}
.panel-grid div{display:flex;flex-direction:column;align-items:center;justify-content:center;gap:10px;font-size:14px;text-align:center;border-right:1px solid rgba(255,255,255,.35);border-bottom:1px solid rgba(255,255,255,.35);line-height:17px}
.panel-grid div:nth-child(3n){border-right:none}
.panel-grid div:nth-child(n+4){border-bottom:none}

/* oxidation */
.oxidation{top:1196px;height:592px;background:radial-gradient(ellipse at 50% 40%,var(--oxid-b) 0,#4e7a7a 40%,var(--oxid-a) 100%)}
.oxidation .section-title{top:50px}
.oxid-copy{position:absolute;left:176px;top:168px;width:510px;font-size:12.5px;line-height:20px}
.oxid-copy ul{list-style:none;margin:22px 0}
.oxid-copy li{font-size:15px;padding-left:28px;position:relative;margin-bottom:14px}
.oxid-copy li::before{content:"";position:absolute;left:2px;top:6px;width:9px;height:9px;border-radius:50%;background:var(--white)}
.molecule-art{position:absolute;left:762px;top:128px;width:281px;height:317px;background:linear-gradient(180deg,rgba(232,199,26,.35),rgba(232,199,26,.6))}
.btn{display:inline-block;background:var(--blue);color:var(--white);font-size:13px;font-weight:700;letter-spacing:1px;text-align:center}
.oxidation .btn{position:absolute;left:522px;top:501px;width:157px;height:38px;line-height:38px}

/* solutions */
.solutions{top:1788px;height:622px;background:var(--blue-band)}
.solutions .section-title{top:30px}
.card{position:absolute;width:428px;height:241px;box-shadow:0 3px 8px rgba(0,0,0,.3)}
.card-art{position:absolute;inset:0}
.card-label{position:absolute;left:0;bottom:44px;background:var(--teal);color:var(--white);font-size:15px;padding:6px 10px}
.card-more{position:absolute;right:6px;bottom:8px;background:var(--teal);color:var(--white);font-size:10px;font-weight:700;letter-spacing:1px;padding:4px 8px}

/* partners */
.partners{top:2410px;height:384px;background:var(--teal)}
.partners .section-title{top:34px}
.partner{position:absolute;top:158px;width:240px;text-align:center;font-size:13px;font-weight:700;line-height:18px}
.partner + .partner::before{content:"";position:absolute;left:-4px;top:-10px;width:1px;height:160px;background:rgba(255,255,255,.35)}
.partner-badge{margin:0 auto 22px;height:100px;display:flex;align-items:center;justify-content:center}
.partner-badge .shape{width:100px;height:100px;border-radius:50%}
.partner-name{font-size:22px;font-weight:500}

/* contact */
.contact{top:2794px;height:596px;background:var(--grey-panel)}
.map-art{position:absolute;inset:0;background:linear-gradient(135deg,#e6e2d6 0,#d7e4c6 40%,#e4e0d3 70%,#cfdcc0 100%);clip-path:polygon(574px 0,1200px 0,1200px 596px,480px 596px)}
.map-edge{position:absolute;left:0;top:0}
.contact-body{position:absolute;left:150px;top:0;width:400px;text-align:center;color:var(--ink)}
.contact-title{margin-top:34px;font-family:"Open Sans",Arial,sans-serif;font-size:22px;font-weight:700;color:var(--blue)}
.contact-title::after{content:"";display:block;width:60px;height:3px;background:var(--blue);margin:10px auto 0}
.contact-intro{margin-top:22px;font-size:12px;line-height:20px}
.contact-cta{margin-top:16px;font-size:12px;color:var(--teal);font-weight:600}
.contact-item{margin-top:22px;font-size:13px;line-height:20px}
.contact-icon{width:26px;height:26px;border-radius:50%;background:var(--teal);margin:0 auto 10px;display:flex;align-items:center;justify-content:center}
.contact .btn{margin-top:26px;padding:0 16px;height:38px;line-height:38px}

/* footer */
.site-footer{top:3390px;height:126px;background:var(--footer)}
.follow{position:absolute;left:162px;top:32px;font-size:11px;font-weight:700}
.socials{display:flex;gap:8px;margin-top:14px}
.socials span{width:26px;height:26px;border-radius:50%;background:var(--blue)}
.socials span:last-child{background:#e8632b}
.footer-nav{position:absolute;right:152px;top:32px;font-size:11px;font-weight:700;text-align:right}
.footer-nav p + p{margin-top:14px}
</style>
</head>
<body>

<header class="section hero">
  <div class="hero-art" role="img" aria-label="Sky and clouds around a ring-shaped earth with a green meadow and tree inside"></div>
  <div class="logo-box"><span class="mark"></span><span class="name">Velqua Research</span></div>
  <nav class="main-nav"><a href="#">HOME</a><a href="#">TECHNOLOGY</a><a href="#">PRODUCTS</a><a href="#">CONTACT</a></nav>
  <p class="hero-tagline">Advanced Oxidation Science for Environmental Pollution Management</p>
  <div class="hero-dots"><span></span><span></span><span></span><span></span></div>
</header>

<section class="section ideas">
  <div class="ideas-art" role="img" aria-label="City skyline reflected in a calm river"></div>
  <h2 class="section-title">NEW IDEAS FOR A CLEANER WORLD</h2>
  <div class="solutions-panel">
    <p class="panel-head">SOLUTIONS</p>
    <div class="panel-tops">
      <div><svg width="30" height="26" viewBox="0 0 30 26" fill="none" stroke="#fff" stroke-width="2"><path d="M4 10h12v4H4zM16 12h6v8M22 22v2"/></svg>WATER</div>
      <div><svg width="30" height="26" viewBox="0 0 30 26" fill="none" stroke="#fff" stroke-width="2"><path d="M3 8q6-4 12 0t12 0M3 14q6-4 12 0t12 0M3 20q6-4 12 0t12 0"/></svg>AIR</div>
      <div><svg width="30" height="26" viewBox="0 0 30 26" fill="#fff"><path d="M15 2q9 12 9 16a9 9 0 0 1-18 0q0-4 9-16z"/></svg>FUEL</div>
    </div>
    <div class="panel-grid">
      <div><svg width="24" height="24" viewBox="0 0 24 24" fill="none" stroke="#fff" stroke-width="2"><path d="M12 3l5 8H7zM4 20h16"/></svg>Environmental</div>
      <div><svg width="24" height="24" viewBox="0 0 24 24" fill="#fff"><circle cx="12" cy="12" r="7"/><circle cx="12" cy="12" r="3" fill="#1c6cc0"/></svg>Pollution Control</div>
      <div><svg width="24" height="24" viewBox="0 0 24 24" fill="none" stroke="#fff" stroke-width="2"><circle cx="12" cy="12" r="9"/><path d="M3 12h18M12 3v18"/></svg>Radical</div>
      <div><svg width="24" height="24" viewBox="0 0 24 24" fill="#fff"><rect x="4" y="4" width="7" height="7"/><rect x="13" y="13" width="7" height="7"/><rect x="4" y="13" width="7" height="7"/></svg>Solutions<br>Employing</div>
      <div><svg width="24" height="24" viewBox="0 0 24 24" fill="#fff"><path d="M4 20Q4 4 20 4Q20 20 4 20z"/></svg>Nature's Most</div>
      <div><svg width="24" height="24" viewBox="0 0 24 24" fill="none" stroke="#fff" stroke-width="2"><path d="M19 8a8 8 0 0 0-14 2M5 16a8 8 0 0 0 14-2M19 3v5h-5M5 21v-5h5"/></svg>Reactive Free</div>
    </div>
  </div>
</section>

<section class="section oxidation">
  <h2 class="section-title">ADVANCED OXIDATION</h2>
  <div class="oxid-copy">
    <p>Advanced Oxidation refers to a variety of techniques employing the Hydroxyl Radical, an energetic, highly reactive cousin of the water molecule:</p>
    <ul>
      <li>To add oxygen to inorganic molecules</li>
      <li>To remove hydrogen from organic molecules</li>
    </ul>
    <p>These transformations convert important industrial contaminants into reactive forms that can be captured or that disintegrate into harmless end products.</p>
  </div>
  <div class="molecule-art" role="img" aria-label="Diagram of hydroxyl radical reactions with labelled molecules"></div>
  <a class="btn" href="#">LEARN MORE</a>
</section>

<section class="section solutions">
  <h2 class="section-title">SOLUTIONS</h2>
  <article class="card" style="left:166px;top:85px">
    <div class="card-art" role="img" aria-label="Refinery towers and pipes" style="background:linear-gradient(180deg,#c9ccd0,#3b3f44)"></div>
    <span class="card-label">Fuel Oil Desulfurization</span><span class="card-more">READ MORE ›</span>
  </article>
  <article class="card" style="left:614px;top:85px">
    <div class="card-art" role="img" aria-label="Worker beside an industrial liquid tank" style="background:linear-gradient(135deg,#2a3550,#6a7880 55%,#c9d0d2)"></div>
    <span class="card-label">Volatile Organic Compunds (VOC)</span><span class="card-more">READ MORE ›</span>
  </article>
  <article class="card" style="left:166px;top:343px">
    <div class="card-art" role="img" aria-label="Smokestacks releasing flue gas" style="background:linear-gradient(180deg,#2b2e55,#6e6a86 60%,#3a3550)"></div>
    <span class="card-label">Flue Gas Scrubbing</span><span class="card-more">READ MORE ›</span>
  </article>
  <article class="card" style="left:614px;top:343px">
    <div class="card-art" role="img" aria-label="Outflow pipe discharging into a stream" style="background:linear-gradient(160deg,#4d6a35,#8a7a52 55%,#5a4a2c)"></div>
    <span class="card-label">Volatile Organic Compunds (VOC)</span><span class="card-more">READ MORE ›</span>
  </article>
</section>

<section class="section partners">
  <h2 class="section-title">OUR PARTNERS</h2>
  <div class="partner" style="left:110px"><div class="partner-badge"><span class="partner-name">Velqua Research</span></div>OUR SALES<br>PARTNER IN CHINA</div>
  <div class="partner" style="left:363px"><div class="partner-badge"><span class="shape" style="background:#d9301f"></span></div>OUR CONSTRUCTION<br>PARTNER IN CHINA</div>
  <div class="partner" style="left:611px"><div class="partner-badge"><span class="shape" style="background:#1d5e8c"></span></div>OUR TECHNOLOGY<br>PARTNER IN CHINA</div>
  <div class="partner" style="left:848px"><div class="partner-badge"><span class="shape" style="background:#b21f2d"></span></div>OUR TECHNOLOGY<br>PARTNER IN CHINA</div>
</section>

<section class="section contact">
  <div class="map-art" role="img" aria-label="Street map around the company office"></div>
  <svg class="map-edge" width="1200" height="596"><line x1="574" y1="0" x2="480" y2="596" stroke="#2bbdb4" stroke-width="3"/></svg>
  <div class="contact-body">
    <h2 class="contact-title">CONTACT</h2>
    <p class="contact-intro">We welcome inquiries regarding the licensing, distribution, and<br>purchase of our products, systems, and technologies.</p>
    <p class="contact-cta">Please contact us for more information.</p>
    <div class="contact-item"><div class="contact-icon"><svg width="12" height="14" viewBox="0 0 12 14" fill="#fff"><path d="M6 0a5 5 0 0 1 5 5c0 4-5 9-5 9S1 9 1 5a5 5 0 0 1 5-5z"/></svg></div>Velqua Research Corporation<br>Harlow Bend, New Jersey, U.S.A.</div>
    <div class="contact-item"><div class="contact-icon"><svg width="14" height="10" viewBox="0 0 14 10" fill="none" stroke="#fff" stroke-width="1.5"><rect x="1" y="1" width="12" height="8"/><path d="M1 1l6 5 6-5"/></svg></div>info@velquaresearch.example</div>
    <div class="contact-item"><div class="contact-icon"><svg width="14" height="14" viewBox="0 0 14 14" fill="#fff"><path d="M3 1l3 3-2 2q1 3 4 4l2-2 3 3-2 2Q4 12 1 3z"/></svg></div>+1 555 010 0147</div>
    <a class="btn" href="#">ABOUT VELQUA RESEARCH</a>
  </div>
</section>

<footer class="section site-footer">
  <div class="follow">FOLLOW US ON<div class="socials"><span></span><span></span><span></span></div></div>
  <div class="footer-nav"><p>HOME &nbsp;/&nbsp; ABOUT US &nbsp;/&nbsp; PRODUCTS &nbsp;/&nbsp; PARTNERS &nbsp;/&nbsp; CONTACT US</p><p>COPYRIGHTS © 2016 ALL RIGHTS RESERVED</p></div>
</footer>

</body>
</html>
```